Looking for a dynamic business card for a pizzeria.

A business card with our food, logo, and space for name, title, email, website, phone. The card should convey quality, unique, amazing. On the front, I envision food photo or photos with the owners names and contact information. On the back, more food with locations, website, facebook, twitter, instagram icons. It should look polished, not cartoonish, or plain.
Target Market(s)
upscale, local food buyers, 30-50 years in age.
Industry/Entity Type
Restaurant
Contact Information for Business Card
Business Name: Bru'nettix, LLC
Website: www.brunettix.com
Back:
2 locations: (can list on the back of card)
1. Harborview
4087 Corlan Avenue
Marlow, WA 98341
360-481-5067
2. Cedar Ridge
7315 Wendmere Road
Marlow, WA 98347
360-293-8840
front:
EDITABLE space for
Business name
Person's Name
title
2nd title
Email address
cell-phone number
Requirements
Must have
- logo
- my food photo or photos (no watermarks showing)
- locations on back
- Person contact information on front
- full bleed

```html
<!DOCTYPE html>
<html lang="en">
<head>
<meta charset="utf-8">
<title>Bru'nettix Business Card</title>
<link href="https://fonts.googleapis.com/css2?family=Montserrat:wght@400;600&family=Didact+Gothic&display=swap" rel="stylesheet">
<style>
  :root {
    --backdrop: #e4e4e4;
    --card-white: #ffffff;
    --brand-red: #b8343a;
    --ink: #1e1e1e;
    --ink-soft: #3a3a3a;
    --rule-grey: #9a9a9a;
    --photo-cured: linear-gradient(135deg, #c46a4a, #8e3b2c 60%, #d9b69a);
    --photo-sandwich: linear-gradient(160deg, #e2c27c, #b9822f 55%, #5f7a34);
    --photo-rolls: linear-gradient(150deg, #d07a3a, #b2482a 55%, #e8c9a4);
    --photo-salad: linear-gradient(140deg, #8fbf4a, #c3573f 55%, #efe2c9);
  }
  * { box-sizing: border-box; margin: 0; padding: 0; }
  html, body { width: 1200px; height: 852px; overflow: hidden; }
  body { background: var(--backdrop); position: relative; font-family: "Didact Gothic", sans-serif; }

  .card {
    position: absolute; top: 91px; width: 386px; height: 658px;
    background: var(--card-white); border-radius: 26px; overflow: hidden;
  }
  .card--locations { left: 108px; padding: 10px; }
  .card--contact { left: 710px; }

  .photo-grid {
    display: grid; width: 100%; height: 100%;
    grid-template-columns: 180px 1fr; grid-template-rows: 318px 1fr; gap: 5px;
    border-radius: 18px; overflow: hidden;
  }
  .photo { width: 100%; height: 100%; }
  .photo--cured { background: var(--photo-cured); }
  .photo--sandwich { background: var(--photo-sandwich); }
  .photo--rolls { background: var(--photo-rolls); }
  .photo--salad { background: var(--photo-salad); }

  .location-badge {
    position: absolute; left: 82px; top: 222px; width: 220px; height: 220px;
    border-radius: 50%; background: var(--brand-red); color: var(--card-white);
    display: flex; flex-direction: column; align-items: center; justify-content: center;
    text-align: center; font-size: 12.5px; line-height: 1.38;
  }
  .location-badge strong { font-family: "Montserrat", sans-serif; font-weight: 600; font-size: 13.5px; }

  .brand {
    position: absolute; top: 100px; left: 0; width: 100%;
    text-align: center;
  }
  .brand-name {
    font-family: "Didact Gothic", sans-serif; font-weight: 400; font-size: 40px;
    color: var(--ink); letter-spacing: 1px;
  }

  .person { position: absolute; top: 276px; width: 100%; text-align: center; }
  .person-name { font-family: "Montserrat", sans-serif; font-weight: 400; font-size: 25px; color: var(--ink); letter-spacing: 1.5px; }
  .person-title { font-size: 17px; color: var(--ink-soft); margin-top: 4px; }

  .contact-list { position: absolute; top: 395px; width: 100%; list-style: none; text-align: center; font-size: 16px; color: var(--ink); letter-spacing: 2px; }
  .contact-list li { display: flex; align-items: center; justify-content: center; gap: 8px; height: 32px; }
  .contact-list svg { width: 18px; height: 18px; flex: none; }
  .contact-list .contact-address { display: block; height: auto; line-height: 1.75; letter-spacing: 0.8px; margin-top: 4px; }

  .web-band {
    position: absolute; top: 592px; left: 0; width: 100%; height: 36px;
    background: var(--brand-red); color: var(--card-white);
    display: flex; align-items: center; justify-content: center;
    font-size: 17px; letter-spacing: 2px;
  }
  .web-rule { position: absolute; top: 634px; left: 0; width: 100%; height: 4px; background: var(--rule-grey); }
</style>
</head>
<body>

<section class="card card--locations">
  <div class="photo-grid">
    <div class="photo photo--cured" role="img" aria-label="Photo of hands arranging cured meats on pizza dough"></div>
    <div class="photo photo--sandwich" role="img" aria-label="Photo of a grilled flatbread sandwich with greens"></div>
    <div class="photo photo--rolls" role="img" aria-label="Photo of baked rolls topped with tomato sauce"></div>
    <div class="photo photo--salad" role="img" aria-label="Photo of a fresh salad with sliced meat"></div>
  </div>
  <div class="location-badge">
    <strong>Harborview</strong>
    <span>4087 Corlan Avenue</span>
    <span>Marlow, WA 98341</span>
    <span>360-481-5067</span>
    <strong>Cedar Ridge</strong>
    <span>7315 Wendmere Road</span>
    <span>Marlow, WA 98347</span>
    <span>360-293-8840</span>
  </div>
</section>

<section class="card card--contact">
  <div class="brand">
    <span class="brand-name">Bru'nettix</span>
  </div>

  <div class="person">
    <h1 class="person-name">MARCUS VELLANO</h1>
    <p class="person-title">Managing Director</p>
  </div>

  <ul class="contact-list">
    <li>
      <svg viewBox="0 0 20 20" aria-hidden="true"><circle cx="10" cy="10" r="10" fill="#1e1e1e"/><path d="M6.5 5.5l2 0 1 2.5-1.3 1a6 6 0 0 0 2.8 2.8l1-1.3 2.5 1v2a1 1 0 0 1-1 1A8 8 0 0 1 5.5 6.5a1 1 0 0 1 1-1z" fill="#fff"/></svg>
      <span>360 518 2274</span>
    </li>
    <li>
      <svg viewBox="0 0 20 20" aria-hidden="true"><circle cx="10" cy="10" r="10" fill="#1e1e1e"/><rect x="7" y="4.5" width="6" height="11" rx="1" fill="#fff"/><rect x="8" y="6" width="4" height="7" fill="#1e1e1e"/></svg>
      <span>360 518 2274</span>
    </li>
    <li>
      <svg viewBox="0 0 20 20" aria-hidden="true"><circle cx="10" cy="10" r="10" fill="#1e1e1e"/><rect x="5" y="6.5" width="10" height="7" fill="#fff"/><path d="M5 6.5l5 4 5-4" fill="none" stroke="#1e1e1e" stroke-width="1"/></svg>
      <span>marcus@brunettix.com</span>
    </li>
    <li class="contact-address">4087 Corlan Avenue, Suite 2<br>Marlow</li>
  </ul>

  <div class="web-band">www.brunettix.com</div>
  <div class="web-rule"></div>
</section>

</body>
</html>
```